Keystonery Billboard - Financial Services Company (Investments, Tax Planning and Insurance)

Our new office has a billboard directly above the office building. We'd like something eye-catching with a strong Call to Action, with the main part of the billboard being under 7 words if possible. We'd like you to include a way to get ahold of us (either our website keystoneryllc.example or our phone number 302-418-2907. You may also include in small font something to indicate that we've been serving the area since 1980 (the DE area, the tri-state area, the Marlowe Hollow, etc.)

We offer financial planning, tax planning, and insurance, and we help our clients to focus on their goals and happiness by providing everything they need for lifelong wealth under one roof.

Our logos are attached, we use a triangle logo with green and gray. We use the tagline "discover lasting prosperity" but this does not need to be included.

Potential ideas we have seen from other financial companies-
- the concept that the driver spends more time looking at billboards than planning for their retirement
-something along the lines of "everything you need for your finances is in this building right here" planning, investments, taxes, insurance"
-don't spend your time worrying about retirement, let us help you plan for it
-are you working for your money, or is it working for you?
- retirement takes planning, we're here to help
- ready to retire? talk to us
- need investment advice?
- need help investing?
- crossing your fingers isn't a retirement plan. we can help.
- retiring soon? you need help.

Those are just general ideas, please feel free to be creative.

brand colors:
#00b585
#00b185
#000000
#ffffff
#6d6f75
#6d6f75
#6f7074
#021712
#052e24

```html
<!DOCTYPE html>
<html lang="en">
<head>
<meta charset="utf-8">
<title>Keystonery Billboard</title>
<link href="https://fonts.googleapis.com/css2?family=Anton&family=Poppins:wght@400;600;700&display=swap" rel="stylesheet">
<style>
  :root {
    --brand-green: #00b585;
    --deep-green: #052e24;
    --ink: #021712;
    --gray: #6d6f75;
    --white: #ffffff;
    --page: #ffffff;
  }
  * { margin: 0; padding: 0; box-sizing: border-box; }
  html, body {
    width: 1199px;
    height: 1200px;
    overflow: hidden;
    background: var(--page);
  }
  .canvas {
    position: relative;
    width: 1199px;
    height: 1200px;
  }
  .billboard {
    position: absolute;
    left: 50px;
    top: 440px;
    width: 1100px;
    height: 321px;
    box-shadow: 0 8px 18px rgba(0, 0, 0, 0.18);
    overflow: hidden;
  }
  .billboard__panels {
    position: absolute;
    inset: 0;
  }
  .brand {
    position: absolute;
    left: 16px;
    top: 112px;
    width: 320px;
    text-align: center;
  }
  .brand__name {
    font-family: "Poppins", sans-serif;
    font-weight: 600;
    font-size: 44px;
    line-height: 1;
    color: var(--brand-green);
  }
  .brand__tagline {
    margin-top: 8px;
    font-family: "Poppins", sans-serif;
    font-weight: 400;
    font-size: 10px;
    letter-spacing: 3.6px;
    text-transform: uppercase;
    color: var(--gray);
  }
  .contact-phone {
    position: absolute;
    left: 29px;
    top: 212px;
    font-family: "Anton", sans-serif;
    font-size: 62px;
    line-height: 1;
    color: var(--ink);
  }
  .headline {
    font-family: "Anton", sans-serif;
    font-weight: 400;
    text-transform: uppercase;
  }
  .headline__line {
    position: absolute;
    left: 415px;
    display: block;
    font-size: 86px;
    line-height: 1;
    letter-spacing: 0;
    white-space: nowrap;
    transform-origin: left top;
  }
  .headline__question {
    top: 26px;
    color: var(--white);
    transform: scaleX(1.28);
  }
  .headline__answer {
    top: 117px;
    color: var(--ink);
    transform: scaleX(1.18);
  }
  .services {
    position: absolute;
    left: 397px;
    top: 236px;
    width: 676px;
    font-family: "Poppins", sans-serif;
  }
  .services__intro {
    font-size: 19.5px;
    font-weight: 400;
    color: var(--brand-green);
    white-space: nowrap;
  }
  .services__list {
    display: flex;
    justify-content: space-between;
    list-style: none;
    margin-top: 4px;
  }
  .services__item {
    display: flex;
    align-items: center;
    gap: 8px;
    font-size: 22px;
    font-weight: 700;
    color: var(--white);
    text-transform: uppercase;
  }
  .services__tick { width: 16px; height: 16px; flex: none; }
</style>
</head>
<body>
<div class="canvas">
  <section class="billboard" aria-label="Keystonery retirement planning billboard">
    <svg class="billboard__panels" width="1100" height="321" viewBox="0 0 1100 321" aria-hidden="true">
      <rect width="1100" height="321" fill="var(--white)"/>
      <polygon points="256,0 1100,0 1100,222 377,222" fill="var(--brand-green)"/>
      <polygon points="377,222 1100,222 1100,321 324,321" fill="var(--deep-green)"/>
    </svg>

    <div class="brand">
      <div class="brand__name">Keystonery</div>
      <div class="brand__tagline">Discover lasting prosperity</div>
    </div>

    <div class="contact-phone">302-418-2907</div>

    <h1 class="headline">
      <span class="headline__line headline__question">Retiring soon?</span>
      <span class="headline__line headline__answer">You need help</span>
    </h1>

    <div class="services">
      <p class="services__intro">Everything you need for your finances is in this building right here</p>
      <ul class="services__list">
        <li class="services__item">
          <svg class="services__tick" viewBox="0 0 16 16"><rect x="1" y="1" width="14" height="14" rx="2" fill="none" stroke="var(--brand-green)" stroke-width="1.6"/><path d="M4.5 8.2l2.4 2.4 4.6-5" fill="none" stroke="var(--brand-green)" stroke-width="1.6"/></svg>
          Planning
        </li>
        <li class="services__item">
          <svg class="services__tick" viewBox="0 0 16 16"><rect x="1" y="1" width="14" height="14" rx="2" fill="none" stroke="var(--brand-green)" stroke-width="1.6"/><path d="M4.5 8.2l2.4 2.4 4.6-5" fill="none" stroke="var(--brand-green)" stroke-width="1.6"/></svg>
          Investments
        </li>
        <li class="services__item">
          <svg class="services__tick" viewBox="0 0 16 16"><rect x="1" y="1" width="14" height="14" rx="2" fill="none" stroke="var(--brand-green)" stroke-width="1.6"/><path d="M4.5 8.2l2.4 2.4 4.6-5" fill="none" stroke="var(--brand-green)" stroke-width="1.6"/></svg>
          Taxes
        </li>
        <li class="services__item">
          <svg class="services__tick" viewBox="0 0 16 16"><rect x="1" y="1" width="14" height="14" rx="2" fill="none" stroke="var(--brand-green)" stroke-width="1.6"/><path d="M4.5 8.2l2.4 2.4 4.6-5" fill="none" stroke="var(--brand-green)" stroke-width="1.6"/></svg>
          Insurance
        </li>
      </ul>
    </div>
  </section>
</div>
</body>
</html>
```